Professional violinist needs business cards

I am trying to attract the following jobs:
-private violin lessons (primarily classical)
-performance gigs (weddings, birthday parties, funerals, etc.)
-collaborations with other artists (studio recordings, performances)

I want to communicate that I have a very high standard of excellence for my work, but I also love people and celebrations.
Values/style words I like are:
love, joy, peace, fun, beauty, authenticity, excellence, warmth, refined/sleek, free spirited. If that's too confusing, just ignore :)

I will attach my favorite business card template that I could find on Canva. The lines are supposed to be like a music staff, which I think is really cool, but I also don't want it to look too busy. I like the simple black and white--I think it looks sharp--but I also am open to other ideas. I also have seen business cards with pictures included that looked great, so I attached an image that could be used as well.

I am also attaching a file that I made of my initials that could be used as a logo, but I'm not sure if it should be included.

Information on the card:
-My name (18 letters total)
-"violinist"
-phone number, email, website

Thank you!

```html
<!DOCTYPE html>
<html lang="en">
<head>
<meta charset="utf-8">
<title>Helena Marchetti – Violinist Business Cards</title>
<link href="https://fonts.googleapis.com/css2?family=Dancing+Script:wght@500&family=Lora:wght@400;500&display=swap" rel="stylesheet">
<style>
  :root {
    --backdrop: #2a2a2a;
    --card: #1f2328;
    --card-deep: #1a1d21;
    --gold: #cbb892;
    --ink: #ece8df;
    --photo-dark: #2b2620;
    --photo-mid: #5c5244;
  }
  html, body {
    margin: 0;
    padding: 0;
    width: 1200px;
    height: 1138px;
    overflow: hidden;
    background: var(--backdrop);
  }
  .canvas {
    position: relative;
    width: 1200px;
    height: 1138px;
  }
  .card {
    position: absolute;
    border-radius: 16px;
    overflow: hidden;
    background: linear-gradient(180deg, var(--card) 0%, var(--card-deep) 100%);
    box-shadow: 0 6px 14px rgba(0,0,0,0.45);
  }
  .card--front { left: 274px; top: 186px; width: 622px; height: 376px; }
  .card--back  { left: 276px; top: 608px; width: 618px; height: 374px; }

  .portrait {
    position: absolute;
    left: 0; top: 0;
    width: 240px; height: 100%;
    background:
      linear-gradient(90deg, rgba(31,35,40,0) 0%, rgba(31,35,40,0) 80%, var(--card) 100%),
      linear-gradient(160deg, var(--photo-mid) 0%, var(--photo-dark) 55%, #15130f 100%);
  }

  .mark {
    position: absolute;
    border: 2px solid var(--gold);
    border-radius: 50%;
    box-sizing: border-box;
  }
  .card--front .mark { left: 406px; top: 114px; width: 44px; height: 44px; }
  .card--back .mark  { left: 114px; top: 88px; width: 56px; height: 56px; }

  .name {
    position: absolute;
    margin: 0;
    font-family: "Dancing Script", cursive;
    font-weight: 500;
    color: var(--ink);
    white-space: nowrap;
    line-height: 1;
    letter-spacing: 0.5px;
  }
  .card--front .name { left: 290px; width: 290px; top: 180px; font-size: 37px; text-align: center; }
  .card--back .name  { left: 206px; width: 292px; top: 82px; font-size: 37px; text-align: center; }

  .title-row {
    position: absolute;
    display: flex;
    align-items: center;
    gap: 18px;
  }
  .card--front .title-row { left: 290px; width: 290px; top: 228px; }
  .card--back .title-row  { left: 210px; width: 284px; top: 128px; }
  .title-row .rule {
    flex: 1;
    height: 1px;
    background: var(--gold);
    opacity: 0.8;
  }
  .title-row .role {
    font-family: "Lora", serif;
    font-weight: 500;
    font-size: 16px;
    letter-spacing: 2.5px;
    color: var(--ink);
  }

  .staff-line {
    position: absolute;
    left: 0; right: 0;
    height: 3px;
    background: var(--gold);
  }
  .staff-line--top { top: 21px; }
  .staff-line--bottom { top: 349px; }

  .contact {
    position: absolute;
    left: 0; right: 0;
    top: 198px;
    margin: 0;
    padding: 0;
    list-style: none;
    text-align: center;
    font-family: "Lora", serif;
    font-size: 14.5px;
    line-height: 23.3px;
    color: var(--ink);
  }
  .contact .accent { color: var(--gold); }
</style>
</head>
<body>
<div class="canvas">
  <section class="card card--front">
    <div class="portrait" role="img" aria-label="Portrait of the violinist in a black dress holding her violin beside a stone wall"></div>
    <span class="mark" aria-hidden="true"></span>
    <h1 class="name">Helena Marchetti</h1>
    <div class="title-row">
      <span class="rule"></span>
      <span class="role">VIOLINIST</span>
      <span class="rule"></span>
    </div>
  </section>

  <section class="card card--back">
    <span class="staff-line staff-line--top"></span>
    <span class="mark" aria-hidden="true"></span>
    <h2 class="name">Helena Marchetti</h2>
    <div class="title-row">
      <span class="rule"></span>
      <span class="role">VIOLINIST</span>
      <span class="rule"></span>
    </div>
    <ul class="contact">
      <li>+1 (555) 014-2368</li>
      <li>Helena@HelenaMarchetti.com</li>
      <li>www.<span class="accent">HelenaMarchetti</span>.com</li>
      <li>Cedar Falls, IA</li>
    </ul>
    <span class="staff-line staff-line--bottom"></span>
  </section>
</div>
</body>
</html>
```